Business Card Re-Design/Update

We'd like to update out business cards. I've included our current "Style guide" which has the colour scheme of the organisation in it. I've also included the branding files with logos etc in them.

I've also included a copy of one of our existing cards so that you can see how ugly/dated they look. I'd like a fresh modern corporate look.

Target Market(s)

These are for our clients, potential clients, industry contacts - like all business cards

Contact Information for Business Card

Name
Position
Company Address - Level 1, 47 Fernby Street, Carlow Qld 4072
Direct Phone
mobile
Email
Website -www.korvalit.com.au
Logo

Colors

Designer to choose colors to be used in the design.

Requirements
Must have
• Main Logo
• Cards will need to be editable to be able to personalize them for each new employee.
Nice to have
• The MapOut, ShipWell, KeepSteady would be okay to have if they can be sensibly and professionally added to the look without detracting from the main imagery.
• Maybe they could go on the back of the card? will leave this to your creative discretion as to whether/where they fit.
Should not have
• Should not have decorative or script fonts

```html
<!DOCTYPE html>
<html lang="en">
<head>
<meta charset="utf-8">
<title>korvalit Business Card</title>
<link href="https://fonts.googleapis.com/css2?family=Work+Sans:wght@400;500;600&display=swap" rel="stylesheet">
<style>
  :root {
    --brand-blue: #1b7cc4;
    --ink: #2b2b2b;
    --ink-soft: #4a4a4a;
    --card-dark: #2c2d2f;
    --card-dark-edge: #1f2022;
    --backdrop: #d9dadc;
    --paper: #ffffff;
    --paper-shade: #eef0f2;
  }
  * { box-sizing: border-box; margin: 0; padding: 0; }
  html, body { width: 1200px; height: 900px; overflow: hidden; }
  body {
    background: var(--backdrop);
    font-family: "Work Sans", Arial, sans-serif;
    position: relative;
  }
  .card {
    position: absolute;
    width: 680px;
    height: 388px;
    border-radius: 3px;
    box-shadow: 0 14px 34px rgba(0,0,0,.28);
    overflow: hidden;
  }
  .card-front {
    left: 60px; top: 60px;
    background: linear-gradient(135deg, var(--paper) 40%, var(--paper-shade));
  }
  .front-top-rule {
    position: absolute; top: 0; right: 0;
    width: 58%; height: 3px;
    background: var(--brand-blue);
  }
  .front-base {
    position: absolute; left: 0; bottom: 0; width: 100%; height: 12px;
  }
  .brand {
    position: absolute; left: 56px; top: 160px;
    display: flex; align-items: center; gap: 12px;
  }
  .brand-square { width: 34px; height: 34px; background: var(--brand-blue); }
  .brand-name {
    font-size: 44px; font-weight: 500; color: var(--brand-blue);
    letter-spacing: -0.5px; white-space: nowrap;
  }
  .divider {
    position: absolute; left: 326px; top: 66px;
    width: 2px; height: 248px; background: var(--brand-blue);
  }
  .details {
    position: absolute; left: 352px; top: 62px; right: 24px;
    color: var(--ink);
  }
  .person-name {
    font-size: 28px; font-weight: 600; color: var(--brand-blue);
    text-transform: uppercase; letter-spacing: 0.5px; line-height: 1.1;
    white-space: nowrap;
  }
  .person-role { font-size: 15px; color: var(--ink-soft); margin-top: 4px; }
  .address { font-size: 15px; line-height: 1.35; margin-top: 12px; }
  .contact-list {
    list-style: none; margin-top: 12px;
    font-size: 15px; line-height: 1.55;
  }
  .contact-list li { display: flex; align-items: center; gap: 8px; white-space: nowrap; }
  .contact-list svg { width: 12px; height: 12px; flex: none; fill: var(--brand-blue); }
  .web-accent { color: var(--brand-blue); }

  .card-back {
    left: 460px; top: 452px;
    background: linear-gradient(135deg, var(--card-dark) 50%, var(--card-dark-edge));
    display: flex; align-items: center; justify-content: center;
  }
  .back-brand { display: flex; align-items: center; gap: 16px; }
  .back-brand .brand-square { width: 48px; height: 48px; }
  .back-brand .brand-name { font-size: 72px; }
</style>
</head>
<body>

  <section class="card card-front" aria-label="Business card front">
    <div class="front-top-rule"></div>
    <svg class="front-base" viewBox="0 0 680 12" preserveAspectRatio="none" aria-hidden="true">
      <polygon points="0,0 380,0 368,12 0,12" fill="#1b7cc4"/>
      <polygon points="380,0 680,0 680,12 368,12" fill="#2c2d2f"/>
    </svg>

    <div class="brand">
      <span class="brand-square"></span>
      <span class="brand-name">korvalit</span>
    </div>

    <div class="divider"></div>

    <div class="details">
      <h1 class="person-name">Dana Whitfield</h1>
      <p class="person-role">Business Development Manager</p>
      <p class="address">Level 1, 47 Fernby Street,<br>Carlow Qld 4072</p>
      <ul class="contact-list">
        <li><svg viewBox="0 0 12 12"><rect x="3" y="0" width="6" height="12" rx="1"/></svg><span>+61 (0)400 555 018</span></li>
        <li><svg viewBox="0 0 12 12"><path d="M1 4c0-2 2-3 5-3s5 1 5 3v1H8V4H4v1H1zM2 6h8l1 5H1z"/></svg><span>+61 (0)7 5550 1016</span></li>
        <li><svg viewBox="0 0 12 12"><path d="M2 1l3 0 1 3-2 1c1 2 2 3 3 3l1-2 3 1v3c-6 0-9-4-9-9z"/></svg><span>+61 (0)7 5550 1033</span></li>
        <li><svg viewBox="0 0 12 12"><rect x="3" y="0" width="6" height="4"/><rect x="0" y="4" width="12" height="5" rx="1"/><rect x="3" y="8" width="6" height="4"/></svg><span>+61 (0)7 5550 1003</span></li>
        <li><svg viewBox="0 0 12 12"><path d="M0 2h12v8H0zM1 3l5 4 5-4" fill="none" stroke="#1b7cc4" stroke-width="1.2"/></svg><span>dwhitfield@korvalit.com.au</span></li>
        <li><svg viewBox="0 0 12 12"><circle cx="6" cy="6" r="5.5"/></svg><span>www.<span class="web-accent">korvalit</span>.com.au</span></li>
      </ul>
    </div>
  </section>

  <section class="card card-back" aria-label="Business card back">
    <div class="back-brand">
      <span class="brand-square"></span>
      <span class="brand-name">Varnelo</span>
    </div>
  </section>

</body>
</html>
```